Clear Path Keystone Realty yard sign Logo

UPDATE Design logo for Realty yard sign. 24x24 diamond or 36x24 Rectangle.
Open to all ideas. We are a discount firm but want to project a high end feel. We provide 100% of all services and extensive marketing for 1/2 the fee.
The following info must be on sign
CLEAR PATH KEYSTONE (OR K) REALTY
Doran Pike 547-6093
KeystonePX.com

Target Market(s)

home sellers and buyers

Industry/Entity Type

Real Estate yard sign please see sign attached in gif

Logo Text

Clear Path Keystone Realty OR (K IN PLACE OF KEYSTONE)

Requirements
Must have
• CLEAR PATH KEYSTONE (OR K) REALTY Doran Pike 547-6093 KeystonePX.com FOR SALE (optional)

```html
<!DOCTYPE html>
<html lang="en">
<head>
<meta charset="utf-8">
<title>Clear Path Keystone Realty — Yard Sign</title>
<link rel="stylesheet" href="https://fonts.googleapis.com/css2?family=Cinzel:wght@600&family=Arimo:wght@700&display=swap">
<style>
  :root {
    --backdrop: #1c2a3a;
    --frame-blue: #5b9dc6;
    --ink-blue: #6aaedb;
    --accent-gold: #d8cf86;
  }
  html, body {
    margin: 0;
    padding: 0;
    width: 1200px;
    height: 900px;
    overflow: hidden;
    background: var(--backdrop);
  }
  .sign {
    position: relative;
    width: 1200px;
    height: 900px;
  }
  .sign__frame {
    position: absolute;
    inset: 0;
  }
  .sign__content {
    position: absolute;
    left: 0;
    width: 1200px;
    text-align: center;
  }
  .brand-name {
    top: 392px;
    margin: 0;
    font-family: "Cinzel", "Times New Roman", serif;
    font-weight: 600;
    font-size: 38px;
    line-height: 46px;
    letter-spacing: 1px;
    color: var(--ink-blue);
  }
  .agent-line {
    top: 510px;
    margin: 0;
    font-family: "Arimo", Arial, sans-serif;
    font-weight: 700;
    font-size: 36px;
    color: var(--ink-blue);
  }
  .web-line {
    top: 560px;
    margin: 0;
    font-family: "Arimo", Arial, sans-serif;
    font-weight: 700;
    font-size: 25px;
    color: var(--accent-gold);
  }
</style>
</head>
<body>
  <main class="sign">
    <svg class="sign__frame" width="1200" height="900" viewBox="0 0 1200 900" aria-hidden="true">
      <polygon points="600,120 930,450 600,780 270,450" fill="none" stroke="var(--frame-blue)" stroke-width="16" stroke-linejoin="miter"/>
      <circle class="brand-dot" cx="600" cy="315" r="50" fill="var(--accent-gold)"/>
    </svg>
    <h1 class="sign__content brand-name">Clear Path Keystone<br>Realty</h1>
    <p class="sign__content agent-line">Doran Pike 547-6093</p>
    <p class="sign__content web-line">KeystonePX.com</p>
  </main>
</body>
</html>
```